Our new beauty salon requires a price list brochure

Our beauty clinic is a medical grade skin care clinic. So our salon is very clinical and professional in appearance. I would like the colours to be similar to our logo design with some nice texture or abstract shapes thrown in.
Pricelist, contact details and logo is attached
I would prefer it to be a 3 fold brochure.

Target Market(s)

Females aged 30-50

Colors
85acd3
cedeed
c4c4c4
5c5c5c
000000
ffffff
eea3c7
f9d9e8
dbdbdb

Requirements
Must have
• easy to read

```html
<!DOCTYPE html>
<html lang="en">
<head>
<meta charset="UTF-8">
<title>IPL Hair Removal Price List</title>
<link rel="stylesheet" href="https://fonts.googleapis.com/css2?family=Montserrat:wght@300;400;600&display=swap">
<style>
  :root {
    --paper: #ffffff;
    --ink: #3b4a5c;
    --ink-soft: #55657a;
    --leader: #8fa3bb;
    --edge: #e4e6ea;
    --top-rule: #2b2f36;
  }
  html, body {
    margin: 0;
    padding: 0;
    width: 1200px;
    height: 2542px;
    overflow: hidden;
    background: var(--paper);
  }
  .panel {
    position: relative;
    width: 1200px;
    height: 2542px;
    background: var(--paper);
    font-family: "Montserrat", Arial, sans-serif;
    color: var(--ink);
  }
  .panel-edge {
    position: absolute;
    inset: 0;
    pointer-events: none;
  }
  .title {
    position: absolute;
    left: 172px;
    top: 118px;
    margin: 0;
    font-weight: 300;
    font-size: 84px;
    letter-spacing: 3px;
    color: var(--ink);
    white-space: nowrap;
  }
  .price-list {
    position: absolute;
    left: 177px;
    top: 304px;
    width: 880px;
  }
  .price-group {
    list-style: none;
    margin: 0 0 93px 0;
    padding: 0;
  }
  .price-row {
    display: flex;
    align-items: baseline;
    height: 93px;
    line-height: 93px;
  }
  .treatment {
    font-weight: 300;
    font-size: 49px;
    color: var(--ink-soft);
    white-space: nowrap;
  }
  .leader {
    flex: 1;
    margin: 0 26px 0 22px;
    border-bottom: 3px dotted var(--leader);
    transform: translateY(-8px);
  }
  .price {
    font-weight: 600;
    font-size: 50px;
    color: var(--ink);
    white-space: nowrap;
  }
</style>
</head>
<body>
<div class="panel">
  <svg class="panel-edge" width="1200" height="2542" viewBox="0 0 1200 2542" aria-hidden="true">
    <line x1="560" y1="2" x2="1200" y2="2" stroke="var(--top-rule)" stroke-width="4"/>
    <path d="M14 0 C 4 800, 26 1700, 10 2542" fill="none" stroke="var(--edge)" stroke-width="3"/>
    <line x1="1196" y1="0" x2="1196" y2="2542" stroke="var(--edge)" stroke-width="3"/>
  </svg>

  <h1 class="title">IPL HAIR REMOVAL</h1>

  <div class="price-list">
    <ul class="price-group">
      <li class="price-row"><span class="treatment">Upper lip</span><span class="leader"></span><span class="price">$50</span></li>
      <li class="price-row"><span class="treatment">Chin</span><span class="leader"></span><span class="price">$50</span></li>
      <li class="price-row"><span class="treatment">Cheeks</span><span class="leader"></span><span class="price">$75</span></li>
      <li class="price-row"><span class="treatment">Whole face</span><span class="leader"></span><span class="price">$350</span></li>
    </ul>
    <ul class="price-group">
      <li class="price-row"><span class="treatment">Bikini</span><span class="leader"></span><span class="price">$90</span></li>
      <li class="price-row"><span class="treatment">G String</span><span class="leader"></span><span class="price">$120</span></li>
      <li class="price-row"><span class="treatment">Brazilian</span><span class="leader"></span><span class="price">$150</span></li>
    </ul>
    <ul class="price-group">
      <li class="price-row"><span class="treatment">Underarms</span><span class="leader"></span><span class="price">$90</span></li>
      <li class="price-row"><span class="treatment">Half arm</span><span class="leader"></span><span class="price">$180</span></li>
      <li class="price-row"><span class="treatment">Full arm</span><span class="leader"></span><span class="price">$250</span></li>
      <li class="price-row"><span class="treatment">Half leg</span><span class="leader"></span><span class="price">$290</span></li>
      <li class="price-row"><span class="treatment">Thighs</span><span class="leader"></span><span class="price">$290</span></li>
      <li class="price-row"><span class="treatment">Full leg</span><span class="leader"></span><span class="price">$490</span></li>
    </ul>
    <ul class="price-group">
      <li class="price-row"><span class="treatment">Full back</span><span class="leader"></span><span class="price">$350</span></li>
      <li class="price-row"><span class="treatment">Shoulders</span><span class="leader"></span><span class="price">$180</span></li>
      <li class="price-row"><span class="treatment">Nipples</span><span class="leader"></span><span class="price">$60</span></li>
      <li class="price-row"><span class="treatment">Snail trail</span><span class="leader"></span><span class="price">$50</span></li>
      <li class="price-row"><span class="treatment">Stomach</span><span class="leader"></span><span class="price">$250</span></li>
      <li class="price-row"><span class="treatment">Chest</span><span class="leader"></span><span class="price">$250</span></li>
      <li class="price-row"><span class="treatment">Buttocks</span><span class="leader"></span><span class="price">$200</span></li>
    </ul>
  </div>
</div>
</body>
</html>
```